Fresh, modern, fun business card for pediatric dental practice

Need a business card for fresh, modern, fun pediatric dental practice

Clean look that matches our website's font and colors

We prefer the look of curved corners on business cards

Target Market(s)

parents (mothers) of young children, professionals, mid-high class

Industry/Entity Type

Dental

Contact Information for Business Card

Maplebrook Pediatric Dentistry
482 Quarry Lane
Suite 517
Alder Falls, PA 17990
717.555.0193
www.maplebrookkidsdental.example

Mei-Ran Tsai, DMD
Corinne Walbeck, DMD
(we are working on our email address, but we would like that on the card as well)

Font styles to use
Sans Serif

Requirements
Must have
• All info; we would also like to make cards for individual staff members
• colors from our website and color palatte, attatched
• use same font and design as website for branding
Nice to have
• clean, simple card that has a pop of color
• we would like to see a few designs with our tag line "where smiles get brighter"
• we are not sure if we want to have it on there or not
• we would like to see a few designs incorporating the ribbon graphic on our website where the word WELCOME is

```html
<!DOCTYPE html>
<html lang="en">
<head>
<meta charset="utf-8">
<title>Maplebrook Pediatric Dentistry – Business Card</title>
<link href="https://fonts.googleapis.com/css2?family=Lato:wght@400;700;900&display=swap" rel="stylesheet">
<style>
  :root {
    --backdrop: #1c1c1c;
    --card: #2a2a2a;
    --sun: #f7b524;
    --berry: #c8328f;
    --ink: #f2f2f2;
  }
  * { margin: 0; padding: 0; box-sizing: border-box; }
  html, body {
    width: 1200px; height: 900px; overflow: hidden;
    background: var(--backdrop);
    font-family: "Lato", Arial, sans-serif;
  }
  .canvas {
    position: relative; width: 1200px; height: 900px;
    display: flex; flex-direction: column; align-items: center; justify-content: center; gap: 40px;
  }
  .card {
    position: relative; width: 700px; height: 400px;
    background: var(--card);
    border-radius: 16px;
    box-shadow: 0 12px 30px rgba(0,0,0,.45);
    color: var(--ink);
  }
  /* Front */
  .card--front {
    display: flex; flex-direction: column; align-items: center; justify-content: center;
  }
  .brand-dot {
    width: 54px; height: 54px; border-radius: 50%;
    border: 5px solid var(--sun);
    margin-bottom: 22px;
  }
  .brand-name {
    font-weight: 700; font-size: 36px; color: var(--sun);
    letter-spacing: .5px;
  }
  .front-web {
    margin-top: 46px; font-size: 19px; letter-spacing: 2px; color: var(--ink);
  }
  .front-web .domain { color: var(--sun); }
  /* Back */
  .card--back { display: flex; align-items: center; }
  .back-mark {
    width: 290px; display: flex; flex-direction: column; align-items: center; gap: 18px;
  }
  .back-mark .brand-dot { width: 120px; height: 120px; border-width: 9px; margin: 0; }
  .back-mark .brand-name { font-size: 26px; }
  .divider { width: 3px; height: 210px; background: var(--berry); margin-right: 34px; }
  .contact { font-size: 19px; line-height: 1.3; }
  .person-name {
    font-weight: 700; font-size: 27px; color: var(--sun); letter-spacing: 1.5px; text-transform: uppercase;
  }
  .person-title { font-size: 19px; margin-bottom: 14px; }
  .practice { color: var(--sun); }
  .contact-list { list-style: none; margin-top: 14px; }
  .contact-list li { display: flex; align-items: center; gap: 12px; }
  .contact-list svg { width: 16px; height: 16px; flex: none; }
</style>
</head>
<body>
<main class="canvas">
  <section class="card card--front">
    <span class="brand-dot"></span>
    <h1 class="brand-name">Maplebrook Pediatric Dentistry</h1>
    <p class="front-web">www.<span class="domain">maplebrookkidsdental</span>.example</p>
  </section>

  <section class="card card--back">
    <div class="back-mark">
      <span class="brand-dot"></span>
      <span class="brand-name">Maplebrook</span>
    </div>
    <span class="divider"></span>
    <div class="contact">
      <h2 class="person-name">Corinne Walbeck</h2>
      <p class="person-title">DMD</p>
      <p class="practice">Maplebrook Pediatric Dentistry</p>
      <p>482 Quarry Lane</p>
      <p>Suite 517 Alder Falls, PA 17990</p>
      <ul class="contact-list">
        <li>
          <svg viewBox="0 0 16 16" aria-hidden="true"><path fill="#f7b524" d="M3.5 1l2.5 3-1.5 1.8a9 9 0 0 0 5.7 5.7L12 10l3 2.5-1.3 2.3C7.5 15 1 8.5 1.2 2.3z"/></svg>
          717.555.0193
        </li>
        <li>
          <svg viewBox="0 0 16 16" aria-hidden="true"><rect x="1" y="3" width="14" height="10" rx="1" fill="#f7b524"/><path d="M1.5 3.8L8 9l6.5-5.2" stroke="#2a2a2a" stroke-width="1.4" fill="none"/></svg>
          info@maplebrookkidsdental.example
        </li>
        <li>
          <svg viewBox="0 0 16 16" aria-hidden="true"><g fill="none" stroke="#f7b524" stroke-width="1.4"><circle cx="8" cy="8" r="6.5"/><ellipse cx="8" cy="8" rx="2.8" ry="6.5"/><path d="M1.5 8h13M2.5 4.8h11M2.5 11.2h11"/></g></svg>
          www.maplebrookkidsdental.example
        </li>
      </ul>
    </div>
  </section>
</main>
</body>
</html>
```